Quality Monitoring Company Needs a New Site

We are an established company that has a fair number of clients but the site lacks current design standards that we'd like to keep up with. We'd like to mimic the same style of the site on plinkora.com, vetrumo.com, https://brindlecoffer.com/, etc. We'd also like to make sure the designer understands SEO Silos and how it effects the design elements. Attached is the structure that I'd like to follow for the pages. You don't need to design every single sub-page because they'll probably be fairly similar; however, I want to see at least 1 each. Please use the content on our current site for filler areas. Please try to do a good job of understanding what we do so you can use your best judgement on what is needed to be successful. Use our color scheme and the logo should be the side view but I included the AI just in case.
Updates

I am narrowing down on the field of designs that I have received. There are a lot of similarities between the designs I like and don't like. I'd also like to ensure that some of the inner pages get done in the next 5 days so I can see the creativity that is there as well. That is probably what is next -- getting a few inner pages completed so I can see what you can come up with (not based on our current website) because the current "front pages" are all so good and so close.

Industry/Entity Type

Telecommunications

Colors

Designer to choose colors to be used in the design.

Requirements
Must have
• SEO Silo Look and Feel
• Current Colors
Should not have
• No stockphotos whatsoever. NONE.

```html
<!DOCTYPE html>
<html lang="en">
<head>
<meta charset="utf-8">
<title>Vocalyne — Quality Assurance</title>
<link href="https://fonts.googleapis.com/css2?family=Poppins:wght@400;500;600;700&display=swap" rel="stylesheet">
<style>
  :root {
    --navy: #002c5a;
    --footer: #002d5b;
    --accent: #0eb4ea;
    --text: #3b3b3b;
    --body: #555a60;
    --page: #f5f7fa;
    --white: #ffffff;
    --rule: #1f4a78;
  }
  * { margin: 0; padding: 0; box-sizing: border-box; }
  html, body { width: 1200px; height: 936px; overflow: hidden; }
  body { font-family: "Poppins", sans-serif; background: var(--page); color: var(--text); position: relative; }

  .bg-rings { position: absolute; left: 0; top: 0; width: 1200px; height: 668px; }

  .brand { position: absolute; left: 139px; top: 72px; display: flex; align-items: center; gap: 8px;
    font-size: 20px; font-weight: 600; color: var(--navy); }
  .brand-dot { width: 14px; height: 14px; border-radius: 50%; background: var(--accent); }

  .nav { position: absolute; top: 77px; left: 0; font-size: 12.2px; color: var(--text); }
  .nav a { position: absolute; white-space: nowrap; text-decoration: none; color: inherit; }
  .nav a.active { color: var(--accent); font-weight: 600; }

  .call { position: absolute; left: 904px; top: 64px; display: flex; align-items: center; gap: 8px; }
  .call-icon { width: 38px; height: 38px; border-radius: 50%; background: var(--accent);
    display: flex; align-items: center; justify-content: center; }
  .call-number { font-size: 14.5px; font-weight: 600; color: var(--navy); letter-spacing: .3px; }

  .dropdown { position: absolute; z-index: 2; left: 443px; top: 102px; width: 184px; height: 133px; background: var(--white);
    border-radius: 3px; box-shadow: 0 6px 18px rgba(0,40,90,.08); padding: 7px; }
  .dropdown a { display: block; font-size: 10.6px; color: var(--body); text-decoration: none; padding: 0 10px; height: 29px; line-height: 29px; letter-spacing: .2px; white-space: nowrap; }
  .dropdown a.current { background: var(--accent); color: var(--white); font-weight: 600; border-radius: 2px; margin-bottom: 3px; }

  .intro { position: absolute; left: 139px; top: 188px; width: 480px; }
  .intro h1 { font-size: 30px; font-weight: 700; color: var(--navy); line-height: 1.2; }
  .intro h1 span { color: var(--accent); font-weight: 600; }
  .intro .bar { width: 35px; height: 2px; background: var(--accent); margin: 14px 0 21px; }
  .intro p { margin-left: 4px; font-size: 11.3px; line-height: 19px; color: var(--body); letter-spacing: .2px; margin-bottom: 19px; white-space: nowrap; }
  .checks { list-style: none; margin-left: 4px; margin-top: 0; }
  .checks li { display: flex; align-items: center; gap: 12px; font-size: 11.5px; color: var(--body); height: 32.4px; letter-spacing: .2px; white-space: nowrap; }

  .artwork { position: absolute; left: 640px; top: 159px; width: 451px; height: 427px; border-radius: 12px;
    background: linear-gradient(135deg, #e9f4fc 0%, #cfe6f7 50%, #f7e7c4 100%); }

  .footer { position: absolute; left: 0; top: 668px; width: 1200px; height: 268px; background: var(--footer); color: var(--white); }
  .footer h2 { position: absolute; top: 55px; font-size: 18px; font-weight: 600; color: var(--accent); }
  .links { position: absolute; top: 91px; list-style: none; font-size: 12px; }
  .links li { height: 20.4px; }
  .contact-line { position: absolute; font-size: 13px; display: flex; align-items: flex-start; gap: 9px; }
  .contact-line .lines { line-height: 24px; }
  .footer-brand { position: absolute; left: 940px; top: 52px; width: 110px; display: flex; flex-direction: column; align-items: center; gap: 12px;
    font-size: 18px; font-weight: 600; color: var(--white); }
  .footer-brand .mark { width: 70px; height: 70px; border-radius: 50%; background: var(--accent); }
  .divider { position: absolute; left: 139px; top: 221px; width: 919px; height: 1px; background: var(--rule); }
  .copyright { position: absolute; top: 235px; width: 1200px; text-align: center; font-size: 12.8px; }
</style>
</head>
<body>
  <svg class="bg-rings" viewBox="0 0 1200 668" aria-hidden="true">
    <circle cx="988" cy="155" r="346" fill="#eef5fc"/>
    <circle cx="988" cy="155" r="254" fill="#e2eefb"/>
    <circle cx="988" cy="155" r="170" fill="#f5f7fa"/>
  </svg>

  <div class="brand"><span class="brand-dot"></span>Vocalyne</div>

  <nav class="nav">
    <a style="left:404px">Home</a>
    <a class="active" style="left:463px">Services</a>
    <a style="left:537px">Industries</a>
    <a style="left:620px">Pricing</a>
    <a style="left:683px">Team</a>
    <a style="left:742px">Blog</a>
    <a style="left:793px">Contact Us</a>
  </nav>

  <div class="call">
    <span class="call-icon">
      <svg width="15" height="15" viewBox="0 0 24 24"><path fill="#fff" d="M6.6 10.8a15.1 15.1 0 0 0 6.6 6.6l2.2-2.2a1 1 0 0 1 1-.25 11.4 11.4 0 0 0 3.6.57 1 1 0 0 1 1 1V20a1 1 0 0 1-1 1A17 17 0 0 1 3 4a1 1 0 0 1 1-1h3.5a1 1 0 0 1 1 1c0 1.25.2 2.45.57 3.57a1 1 0 0 1-.25 1z"/></svg>
    </span>
    <span class="call-number">555-014-2273</span>
  </div>

  <div class="dropdown">
    <a class="current">Quality Assurance</a>
    <a>Coaching</a>
    <a>Sales Performance</a>
    <a>Ai Enabled Voice Analytics</a>
  </div>

  <section class="intro">
    <h1>Quality <span>Assurance</span></h1>
    <div class="bar"></div>
    <p>Lorem ipsum dolor sit amet, consectetuer adipiscing elit, sed diam nonummy<br>nibh euismod tincidunt ut laoreet dolore magna aliquam erat volutpat. Ut<br>wisi enim ad minim veniam, quis nostrud exerci tation ullamcorper suscipit<br>lobortis nisl ut aliquip ex ea commodo consequat.</p>
    <p>Lorem ipsum dolor sit amet, consectetuer adipiscing elit, sed diam nonummy<br>nibh euismod tincidunt ut laoreet dolore magna aliquam erat volutpat. Ut<br>wisi enim ad minim veniam, quis nostrud exerci tation</p>
    <ul class="checks">
      <li><svg width="11" height="9" viewBox="0 0 11 9"><path d="M1 4.5l3 3L10 1" stroke="var(--accent)" stroke-width="2" fill="none"/></svg>Consectetuer adipiscing elit sed diam nonummy</li>
      <li><svg width="11" height="9" viewBox="0 0 11 9"><path d="M1 4.5l3 3L10 1" stroke="var(--accent)" stroke-width="2" fill="none"/></svg>Nibh euismod tincidunt ut laoreet dolore magna</li>
      <li><svg width="11" height="9" viewBox="0 0 11 9"><path d="M1 4.5l3 3L10 1" stroke="var(--accent)" stroke-width="2" fill="none"/></svg>Aliquam erat volutpat. Ut wisi enim ad minim veniam</li>
      <li><svg width="11" height="9" viewBox="0 0 11 9"><path d="M1 4.5l3 3L10 1" stroke="var(--accent)" stroke-width="2" fill="none"/></svg>Quis nostrud exerci tation ullamcorper suscipit lobortis</li>
    </ul>
  </section>

  <div class="artwork" role="img" aria-label="Illustration of a team reviewing a large quality-checklist dashboard with charts and tick boxes, surrounded by plants and floating check badges"></div>

  <footer class="footer">
    <h2 style="left:139px">Quick Links</h2>
    <ul class="links" style="left:139px"><li>Home</li><li>Services</li><li>System Details</li><li>Pricing</li></ul>
    <ul class="links" style="left:294px"><li>Team</li><li>Blog</li><li>Contact Us</li><li>Login</li></ul>

    <h2 style="left:460px">Contact Us</h2>
    <div class="contact-line" style="left:462px;top:90px">
      <svg width="11" height="15" viewBox="0 0 12 16" style="margin-top:5px"><path fill="#fff" d="M6 0a6 6 0 0 0-6 6c0 4.5 6 10 6 10s6-5.5 6-10a6 6 0 0 0-6-6zm0 8.3A2.3 2.3 0 1 1 6 3.7a2.3 2.3 0 0 1 0 4.6z"/></svg>
      <div class="lines">4410 Marlow Ave.<br>Brookhaven, CA 90521</div>
    </div>
    <div class="contact-line" style="left:660px;top:90px">
      <svg width="14" height="14" viewBox="0 0 24 24" style="margin-top:5px"><path fill="#fff" d="M6.6 10.8a15.1 15.1 0 0 0 6.6 6.6l2.2-2.2a1 1 0 0 1 1-.25 11.4 11.4 0 0 0 3.6.57 1 1 0 0 1 1 1V20a1 1 0 0 1-1 1A17 17 0 0 1 3 4a1 1 0 0 1 1-1h3.5a1 1 0 0 1 1 1c0 1.25.2 2.45.57 3.57a1 1 0 0 1-.25 1z"/></svg>
      <div class="lines">555-014-2273</div>
    </div>
    <div class="contact-line" style="left:660px;top:125px">
      <svg width="15" height="11" viewBox="0 0 16 12" style="margin-top:7px"><path fill="#fff" d="M0 0h16v12H0z"/><path d="M0 .5l8 6 8-6" stroke="var(--footer)" stroke-width="1.4" fill="none"/></svg>
      <div class="lines">hello@vocalyne.com</div>
    </div>

    <div class="footer-brand"><span class="mark"></span>Vocalyne</div>

    <div class="divider"></div>
    <p class="copyright">Copyright © 2019 VOCALYNE. All Rights Reserved.</p>
  </footer>
</body>
</html>
```